Retractable banner.
Health Check For Pets
Check for Ear Mites
Skin Health
Fleas & Ticks

A space SERVE BY <NAME OF CLINIC>

Ideally contain pictures of cats and dogs

```html
<!DOCTYPE html>
<html lang="en">
<head>
<meta charset="utf-8">
<title>Health Check for Pets – Retractable Banner</title>
<link rel="stylesheet" href="https://fonts.googleapis.com/css2?family=Alfa+Slab+One&family=Montserrat:wght@800&display=swap">
<style>
  :root {
    --green: #15924a;
    --red: #ea1c2a;
    --white: #ffffff;
    --ring: #555558;
    --photo-light: #f1f3f4;
    --photo-mid: #dfe3e6;
    --photo-blue: #3f86c8;
    --photo-dark: #3a3432;
  }
  * { margin: 0; padding: 0; box-sizing: border-box; }
  html, body { width: 1200px; height: 667px; overflow: hidden; background: var(--white); }
  .banner { position: relative; width: 1200px; height: 667px; background: var(--white); overflow: hidden; }
  .banner-art { position: absolute; inset: 0; display: block; }
  .headline { font-family: "Alfa Slab One", "Roboto Slab", Georgia, serif; font-weight: 400; }
  .headline-top { fill: var(--green); font-size: 72px; }
  .headline-bottom { fill: var(--red); font-size: 128px; }
  .check-item { font-family: "Montserrat", Arial, sans-serif; font-weight: 800; font-size: 44px; fill: var(--white); }
  .provider-label { font-family: "Montserrat", Arial, sans-serif; font-weight: 800; font-size: 29px; fill: var(--green); }
  .provider-name { font-family: "Montserrat", Arial, sans-serif; font-weight: 800; font-size: 52px; fill: var(--red); }
</style>
</head>
<body>
<div class="banner">
  <svg class="banner-art" width="1200" height="667" viewBox="0 0 1200 667">
    <defs>
      <linearGradient id="photoTone" x1="0" y1="1" x2="1" y2="0">
        <stop offset="0" stop-color="var(--photo-dark)"/>
        <stop offset="0.3" stop-color="#bdb6b0"/>
        <stop offset="0.55" stop-color="var(--photo-light)"/>
        <stop offset="0.8" stop-color="var(--photo-mid)"/>
        <stop offset="1" stop-color="var(--photo-blue)"/>
      </linearGradient>
      <radialGradient id="miteTone"><stop offset="0" stop-color="#e9dc9a"/><stop offset="1" stop-color="#ffffff"/></radialGradient>
      <radialGradient id="dogTone"><stop offset="0" stop-color="#8fb3e8"/><stop offset="1" stop-color="#ffffff"/></radialGradient>
      <radialGradient id="tickTone"><stop offset="0" stop-color="#8a4e2a"/><stop offset="0.7" stop-color="#c99f83"/><stop offset="1" stop-color="#ffffff"/></radialGradient>
      <clipPath id="bannerClip"><rect width="1200" height="667"/></clipPath>
    </defs>

    <g clip-path="url(#bannerClip)">
      <rect class="check-band" x="0" y="298" width="760" height="187" fill="var(--green)"/>
      <ellipse class="photo-arc" cx="1091" cy="458" rx="414" ry="460" fill="none" stroke="var(--green)" stroke-width="9"/>
      <ellipse class="photo" cx="1091" cy="458" rx="408" ry="454" fill="url(#photoTone)" role="img" aria-label="Photo of a veterinarian checking a small black and white dog on an exam table"/>
    </g>

    <g class="check-markers" fill="var(--white)">
      <polygon points="74,310 124,310 124,333 99,350 74,333"/>
      <polygon points="265,310 315,310 315,333 290,350 265,333"/>
      <polygon points="473,310 523,310 523,333 498,350 473,333"/>
    </g>
    <g class="check-dividers" stroke="var(--white)" stroke-width="3">
      <line x1="184" y1="364" x2="184" y2="460"/>
      <line x1="396" y1="364" x2="396" y2="460"/>
    </g>

    <g class="topic-icons">
      <circle cx="884" cy="107" r="79" fill="var(--white)" stroke="var(--ring)" stroke-width="5"/>
      <circle cx="884" cy="107" r="62" fill="url(#miteTone)" role="img" aria-label="Illustration of an ear mite"/>
      <circle cx="734" cy="212" r="79" fill="var(--white)" stroke="var(--ring)" stroke-width="5"/>
      <circle cx="734" cy="212" r="62" fill="url(#dogTone)" role="img" aria-label="Illustration of a sitting dog"/>
      <circle cx="668" cy="392" r="79" fill="var(--white)" stroke="var(--ring)" stroke-width="5"/>
      <circle cx="668" cy="392" r="62" fill="url(#tickTone)" role="img" aria-label="Illustration of a tick"/>
    </g>

    <g class="headline">
      <text class="headline-top" x="35" y="139" textLength="599" lengthAdjust="spacingAndGlyphs">HEALTH CHECK</text>
      <text class="headline-bottom" x="35" y="252" textLength="599" lengthAdjust="spacingAndGlyphs">FOR PETS</text>
    </g>

    <g class="checks" text-anchor="middle">
      <text class="check-item" x="99" y="404" textLength="86" lengthAdjust="spacingAndGlyphs">EAR</text>
      <text class="check-item" x="99" y="452" textLength="128" lengthAdjust="spacingAndGlyphs">MITES</text>
      <text class="check-item" x="290" y="404" textLength="101" lengthAdjust="spacingAndGlyphs">SKIN</text>
      <text class="check-item" x="290" y="452" textLength="167" lengthAdjust="spacingAndGlyphs">HEALTH</text>
      <text class="check-item" x="498" y="404" textLength="133" lengthAdjust="spacingAndGlyphs">FLEAS</text>
      <text class="check-item" x="498" y="452" textLength="161" lengthAdjust="spacingAndGlyphs">&amp; TICKS</text>
    </g>

    <g class="provider">
      <line x1="35" y1="530" x2="245" y2="530" stroke="var(--green)" stroke-width="3"/>
      <line x1="417" y1="530" x2="626" y2="530" stroke="var(--green)" stroke-width="3"/>
      <text class="provider-label" x="331" y="541" text-anchor="middle" textLength="160" lengthAdjust="spacingAndGlyphs">SERVE BY:</text>
      <text class="provider-name" x="36" y="600" textLength="591" lengthAdjust="spacingAndGlyphs">Green Paw Vet Care CLINIC</text>
    </g>
  </svg>
</div>
</body>
</html>
```